Business Cards for new orthopaedic surgery practice

My husband and I are starting our own orthopaedic surgery practice. We are looking for a business card that is uniform, but one will have my name/title and the other will have his. You can just create one design with my name on it for now. But when I choose your design as the winning design I will ask that you add another copy with his name/title.

We are looking for classy, simple, elite all in one. We like dark blues/a little gold/yellow. Something that goes with our logo. We want our logo incorporated. Here is all the info you need:
Business name: RV Bone & Vitality Center
Location: 38517 North Willowmere Ave
Cedar Harbor, FL 33958
Phone: 954-218-4063
Fax: 954-582-7341
Email: info@myrvbonecare.example

Names: Lydia Vance, M.D.
Board Certified Hand and Upper Extremity Surgeon

Ebo Dansu, M.D.
Board Certified Hip & Knee Replacement/General Orthopaedic Surgeon

Can decide what you want to put on the back. Maybe a slogan:
Grounded in Skill. Centered on You

I am just going to upload our logo. The only thing is if we select you as the winning design, the location, and phone numbers may change. We will need your help to update that once fully solidified.

Industry/Entity Type

Medical

Contact Information for Business Card

Colors
0054AA
0677BA
7BADD7
CADEEF
E8F1F8
0094D4
00A9DD
6FCCEA
C7EBF8
E9F6FB

Requirements
Must have
• class, appeal,
Should not have
• We want to air on the side of masculine if we are looking at masculine vs. feminine feel. But we still want it classy, sophisticated, and something we will love

```html
<!DOCTYPE html>
<html lang="en">
<head>
<meta charset="utf-8">
<title>RV Bone &amp; Vitality Center — Business Card</title>
<link href="https://fonts.googleapis.com/css2?family=Montserrat:wght@400;500;600&family=Tinos:wght@700&display=swap" rel="stylesheet">
<style>
  :root {
    --navy: #1b2a52;
    --navy-light: #2a3c6b;
    --gold: #c39d58;
    --paper: #f3f3f2;
    --stage: #1d1d1d;
    --white: #ffffff;
  }
  * { margin: 0; padding: 0; box-sizing: border-box; }
  html, body {
    width: 1200px; height: 1059px; overflow: hidden;
    background: var(--stage);
    font-family: "Montserrat", Arial, sans-serif;
  }
  .card {
    position: absolute;
    width: 688px; height: 390px;
    border-radius: 18px;
    overflow: hidden;
  }
  .card--front { left: 257px; top: 89px; background: var(--paper); }
  .card--back { left: 254px; top: 548px; width: 693px; height: 392px; background: var(--navy); }

  .wave { position: absolute; left: 0; top: 0; width: 100%; height: 100%; }

  .brand {
    position: absolute;
    left: 34px; top: 72px; width: 180px;
    text-align: center;
    color: var(--navy);
    font-weight: 600; font-size: 17px; line-height: 1.35;
    letter-spacing: 0.08em; text-transform: uppercase;
  }
  .brand-ring {
    display: block; width: 14px; height: 14px; margin: 0 auto 10px;
    border: 2px solid var(--gold); border-radius: 50%;
  }

  .doctor {
    position: absolute; right: 37px; top: 34px; text-align: right;
  }
  .doctor-name {
    font-family: "Tinos", "Times New Roman", serif;
    font-weight: 700; font-size: 26px; color: var(--gold);
    letter-spacing: 0.01em; line-height: 1.1;
  }
  .doctor-title {
    margin-top: 6px;
    font-size: 15px; line-height: 21px; color: #2b2b2b;
  }

  .contact {
    position: absolute; right: 37px; top: 210px;
    text-align: right; color: var(--white);
    font-size: 15.5px;
  }
  .contact-address { line-height: 24px; margin-bottom: 20px; }
  .contact-line {
    display: flex; justify-content: flex-end; align-items: center;
    gap: 7px; height: 27px;
  }
  .contact-icon { width: 13px; height: 13px; fill: var(--gold); }

  .back-brand {
    position: absolute; left: 0; right: 0; top: 120px;
    text-align: center; color: var(--navy-light);
    font-weight: 600; font-size: 26px; line-height: 1.35;
    letter-spacing: 0.1em; text-transform: uppercase;
  }
  .back-brand .brand-ring { border-color: var(--navy-light); width: 18px; height: 18px; }
  .slogan {
    position: absolute; left: 0; right: 0; top: 333px;
    text-align: center; color: var(--gold);
    font-weight: 500; font-size: 19px;
  }
</style>
</head>
<body>

<section class="card card--front">
  <svg class="wave" viewBox="0 0 690 392" preserveAspectRatio="none" aria-hidden="true">
    <path fill="var(--gold)" d="M0,240 C60,282 110,302 175,302 C300,298 420,182 520,150 C580,130 640,138 690,162 L690,392 L0,392Z"/>
    <path fill="var(--paper)" d="M0,256 C60,292 110,312 175,312 C300,306 420,194 520,162 C580,144 640,150 690,176 L690,392 L0,392Z"/>
    <path fill="var(--navy)" d="M0,264 C60,300 110,318 175,318 C300,312 420,202 520,170 C580,152 640,158 690,184 L690,392 L0,392Z"/>
  </svg>

  <div class="brand">
    <span class="brand-ring"></span>
    RV Bone &amp;<br>Vitality<br>Center
  </div>

  <div class="doctor">
    <h1 class="doctor-name">LYDIA VANCE, M.D.</h1>
    <p class="doctor-title">Board Certified Hand and Upper<br>Extremity Surgeon</p>
  </div>

  <div class="contact">
    <p class="contact-address">38517 North Willowmere Ave<br>Cedar Harbor, FL 33958</p>
    <p class="contact-line">954-218-4063
      <svg class="contact-icon" viewBox="0 0 24 24" aria-label="Phone"><path d="M6.6 10.8a15.1 15.1 0 0 0 6.6 6.6l2.2-2.2a1 1 0 0 1 1-.25 11.4 11.4 0 0 0 3.6.57 1 1 0 0 1 1 1V20a1 1 0 0 1-1 1A17 17 0 0 1 3 4a1 1 0 0 1 1-1h3.5a1 1 0 0 1 1 1c0 1.25.2 2.45.57 3.57a1 1 0 0 1-.25 1z"/></svg>
    </p>
    <p class="contact-line">954-582-7341
      <svg class="contact-icon" viewBox="0 0 24 24" aria-label="Fax"><path d="M7 3h10v5H7zM4 9h16a2 2 0 0 1 2 2v6h-4v4H6v-4H2v-6a2 2 0 0 1 2-2zm4 7v3h8v-3z"/></svg>
    </p>
    <p class="contact-line">info@myrvbonecare.example
      <svg class="contact-icon" viewBox="0 0 24 24" aria-label="Email"><path d="M2 5h20v14H2zm2 2v.4l8 5.2 8-5.2V7zm0 2.8V17h16V9.8l-8 5.2z"/></svg>
    </p>
  </div>
</section>

<section class="card card--back">
  <div class="back-brand">
    <span class="brand-ring"></span>
    RV Bone &amp;<br>Vitality Center
  </div>
  <p class="slogan">Grounded in Skill. Centered on You</p>
</section>

</body>
</html>
```